Mobile welding fabrication and repair, heavy equipment and semi repair

We need a business card design that will catch the eye but look prelesional at the same time. Were based out of Idaho and we do all welding fabrication jobs and repairs, we also build and install custom pipe fences for personal or larger scale fence jobs and can give free quotes. We can do semi truck and trailer repairs Mobily also.

Target Market(s)

Welding

Industry/Entity Type

welding and repair

Contact Information for Business Card

email (ravenforgeandmend@mailbay.net, phone number 208-417-3826, owner (Dalton Whitcomb), Pipe Fence, Semi Repair, Mobile welding and fabrication

Font styles to use
Sans Serif

Requirements
Must have
• My logo in black background on one side , and other side my logo in white back round with all the information listed on card details
Nice to have
• make it stand out from other business cards

```html
<!DOCTYPE html>
<html lang="en">
<head>
<meta charset="utf-8">
<title>Raven Forge and Mend – Business Card</title>
<link rel="stylesheet" href="https://fonts.googleapis.com/css2?family=Open+Sans:ital,wght@0,400;0,600;0,800;1,400&family=Arimo:wght@400&display=swap">
<style>
  :root {
    --page-bg: #0d0d0e;
    --card-bg: #242527;
    --card-bg-deep: #1e1f21;
    --brand-blue: #1a78d6;
    --edge-blue: #0f5fb8;
    --text-light: #e6e7e9;
    --text-muted: #bfc1c5;
    --rule: #55575b;
  }
  * { box-sizing: border-box; margin: 0; padding: 0; }
  html, body {
    width: 1200px; height: 820px; overflow: hidden;
    background: var(--page-bg);
    font-family: "Open Sans", sans-serif;
  }
  .canvas {
    position: relative; width: 1200px; height: 820px;
    display: flex; align-items: center; justify-content: center; gap: 50px;
  }
  .card {
    position: relative; width: 540px; height: 310px;
    background: linear-gradient(160deg, var(--card-bg), var(--card-bg-deep));
    border-bottom: 4px solid var(--edge-blue);
    border-left: 2px solid var(--edge-blue);
    box-shadow: 0 14px 30px rgba(0,0,0,.6);
  }
  .brand {
    position: absolute;
    font-weight: 800; color: var(--brand-blue);
    text-transform: uppercase; line-height: 1.05; letter-spacing: .04em;
  }
  .brand-mark {
    display: inline-block; width: 12px; height: 12px;
    background: var(--brand-blue); margin-right: 8px; vertical-align: middle;
  }
  /* Front */
  .card-front .brand { top: 62px; right: 60px; font-size: 28px; }
  .card-front .divider {
    position: absolute; left: 170px; right: 40px; top: 160px;
    height: 1px; background: var(--rule);
  }
  .person { position: absolute; left: 40px; top: 176px; }
  .person-name {
    color: var(--brand-blue); font-weight: 600; font-size: 22px;
    text-transform: uppercase; letter-spacing: .01em;
  }
  .person-role {
    color: var(--text-light); font-style: italic; font-size: 16px;
    text-transform: uppercase; margin-top: 2px;
  }
  .contact {
    position: absolute; left: 40px; top: 244px; list-style: none;
    font-family: "Arimo", sans-serif; color: var(--text-light); font-size: 15px;
  }
  .contact li { display: flex; align-items: center; gap: 10px; margin-bottom: 6px; }
  .contact svg { width: 16px; height: 16px; flex: none; }
  /* Back */
  .services {
    position: absolute; top: 40px; right: 70px; list-style: none;
    color: var(--text-light); font-size: 13px; text-transform: uppercase;
  }
  .services li { display: flex; align-items: center; gap: 8px; margin-bottom: 4px; }
  .services li::before {
    content: ""; width: 6px; height: 6px; border-radius: 50%;
    background: var(--brand-blue);
  }
  .card-back .brand { bottom: 56px; right: 44px; font-size: 24px; text-align: left; }
</style>
</head>
<body>
<main class="canvas">
  <section class="card card-front" aria-label="Card front">
    <div class="brand"><span class="brand-mark"></span>Raven Forge<br>and Mend</div>
    <div class="divider"></div>
    <div class="person">
      <p class="person-name">Dalton Whitcomb</p>
      <p class="person-role">Owner</p>
    </div>
    <ul class="contact">
      <li>
        <svg viewBox="0 0 16 16" aria-hidden="true"><path d="M3 1.5l3 .5 1 3-2 1.3a8 8 0 0 0 4.7 4.7L11 9l3 1 .5 3-2 1.5C7 14 2 9 1.5 3.5z" fill="#1a78d6"/></svg>
        <span>208-417-3826</span>
      </li>
      <li>
        <svg viewBox="0 0 16 16" aria-hidden="true"><rect x="1" y="3" width="14" height="10" fill="#1a78d6"/><path d="M1 3l7 6 7-6" fill="none" stroke="#cfe3fa" stroke-width="1.2"/></svg>
        <span>ravenforgeandmend@mailbay.net</span>
      </li>
    </ul>
  </section>

  <section class="card card-back" aria-label="Card back">
    <ul class="services">
      <li>Pipe Fence</li>
      <li>Semi Repair</li>
      <li>Mobile Welding</li>
      <li>Fabrication</li>
    </ul>
    <div class="brand"><span class="brand-mark"></span>Raven Forge<br>and Mend</div>
  </section>
</main>
</body>
</html>
```